custom hat sales

🎨 Project Title:
Custom hat Designer Web Page for WooCommerce (French Texts Provided) i show you exemple what i need

📄 Project Description:
We are looking to create a web page design (desktop and mobile) for a custom cap ordering experience. This page will be integrated into our existing WooCommerce transactional site. The goal is to allow customers to configure and order personalized caps easily and visually.

The entire interface will ultimately be in French, but you can design using placeholder texts (we will provide the actual French text later).

💡 Page Goals & Features:
The page should be modern, clean, and conversion-oriented, and include the following features:

Header area:

Visually showcase examples of designed caps (carousel or grid layout)

A clear title and short description

Customization Steps (in order):

Material selection: users choose the type of material for the cap

Cap color: users choose the base color of the cap

Patch shape: users select the shape of the patch (e.g., round, square, rectangle, custom)

Patch location: mainly the front, but possibly add other options

Quantity selection: users choose how many units they want (with price updates)

Price display: show price per unit and total cost depending on quantity

Call to Action (CTA):

Add to cart or request a quote button

Smooth integration with WooCommerce logic (cart, checkout, etc.)

Other Optional Sections:

FAQ

Delivery timeline

Client testimonials or reviews

🛠 Technical Notes:
The design must be compatible with WooCommerce

Responsive design for both desktop and mobile

The final output can be delivered in Figma, Adobe XD, or layered PSD (no coding required for now)

We will handle the French translation; just use placeholder text where needed

🖼 Inspiration / Style:
Clean and modern layout

Easy to navigate

Visual configurator-style approach (like t-shirt or shoe customization sites)

Feel free to use mockups of caps to enhance the presentation

📎 What we will provide:
Actual French text

Product images (caps, patch styles, color swatches)

Brand logo and colors

Optional references if needed

✅ Deliverables:
Homepage (or dedicated product page) layout

Mobile and desktop views

Editable design file (Figma, XD, PSD)

i need very nice 1 or 2 hat design to present to customer design un der the hat and front and see coupple of shape of the patche to show option possible

```html
<!DOCTYPE html>
<html lang="en">
<head>
<meta charset="utf-8">
<title>Custom Hat – Design Your Own Cap</title>
<link href="https://fonts.googleapis.com/css2?family=Montserrat:wght@300;400;500;600;700;800;900&display=swap" rel="stylesheet">
<style>
:root{
  --green:#5b9a85;
  --yellow:#fcd535;
  --ink:#222222;
  --text:#3a3a3a;
  --mint:#e9f2ee;
  --line:#9fb9b0;
  --straw:#d9bf8a;
  --straw-dark:#b8995e;
  --black:#050505;
  --white:#ffffff;
}
*{box-sizing:border-box;margin:0;padding:0}
html,body{width:1200px;height:3215px;overflow:hidden}
body{font-family:"Montserrat",sans-serif;color:var(--text);background:var(--white);position:relative}
.abs{position:absolute}
section,header,footer{position:absolute;left:0;width:1200px}

/* hero */
.hero{top:0;height:621px;background:var(--green)}
.brand{left:151px;top:30px;font-size:25px;font-weight:700;color:var(--white)}
.cart{left:968px;top:24px}
.cart-badge{left:990px;top:23px;width:16px;height:16px;border-radius:50%;background:var(--yellow);font-size:10px;font-weight:700;color:var(--ink);text-align:center;line-height:16px}
.menu{left:1026px;top:32px}
.hero-title{left:150px;top:134px;width:450px;font-size:70px;font-weight:800;line-height:67px;color:var(--white);letter-spacing:-1px;white-space:nowrap}
.hero-title .accent{color:var(--yellow)}
.hero-sub{left:151px;top:364px;font-size:21px;line-height:32px;color:var(--white);font-weight:400}
.btn-hero{left:150px;top:462px;width:216px;height:53px;border-radius:27px;background:var(--yellow);color:var(--ink);font-size:16px;font-weight:700;text-align:center;line-height:53px}
.tile{border-radius:11px;width:205px;height:201px;overflow:hidden}
.t1{left:628px;top:106px;background:linear-gradient(135deg,#c9a877,#8e6a3e)}
.t2{left:846px;top:106px;background:linear-gradient(180deg,#7fc3e6 0%,#4aa2c8 40%,#efe9dc 100%)}
.t3{left:628px;top:321px;background:linear-gradient(135deg,#3a5e6a,#b98b5e 60%,#2c4148)}
.t4{left:846px;top:321px;background:var(--white)}
.t4-img{left:862px;top:345px;width:173px;height:150px;border-radius:8px;background:linear-gradient(135deg,#efe3c4 0%,var(--straw) 55%,#f3dc72 100%)}
.dot{top:569px;width:12px;height:12px;border-radius:50%;border:2px solid var(--white)}
.dot.on{background:var(--yellow);border-color:var(--yellow)}

/* builder */
.builder{top:621px;height:1019px}
.card{left:152px;top:62px;width:898px;height:885px;background:var(--white);border-radius:12px;box-shadow:0 6px 28px rgba(0,0,0,.09)}
.divider-v{left:532px;top:62px;width:1px;height:885px;background:#ececec}
.build-title{left:197px;top:104px;font-size:37px;font-weight:800;line-height:45px;color:var(--ink)}
.build-title .accent{color:var(--yellow)}
.build-rule{left:201px;top:213px;width:53px;height:2px;background:var(--ink)}
.hat-preview{left:194px;top:270px;width:299px;height:180px;border-radius:12px;background:linear-gradient(180deg,#efe4c9 0%,var(--straw) 60%,#f0d35a 100%)}
.step-num{width:30px;height:30px;border-radius:50%;background:var(--yellow);font-size:13px;font-weight:700;color:var(--ink);text-align:center;line-height:30px}
.step-title{font-size:17px;font-weight:600;color:var(--ink)}
.opt{width:105px;height:71px;border:1px solid #d6d6d6;border-radius:5px;background:var(--white)}
.opt.sel{border:2px solid var(--green);background:#eef5f2}
.opt-img{position:absolute;left:9px;top:8px;width:85px;height:53px;border-radius:4px}
.opt-label{width:105px;text-align:center;font-size:12px;color:var(--text);white-space:nowrap}
.opt-label.sel{color:var(--green);font-weight:600}
.check{width:20px;height:20px}
.slider{left:572px;top:328px;width:440px;height:6px;border-radius:3px;background:linear-gradient(90deg,#ff0000,#ff9900,#ffee00,#33dd00,#00ccff,#0033ff,#aa00ff,#ff00aa,#ff0000)}
.knob{left:614px;top:322px;width:16px;height:16px;border-radius:50%;background:#f5a623;border:2px solid var(--white);box-shadow:0 0 2px rgba(0,0,0,.4)}
.swatch{left:571px;top:357px;width:21px;height:21px;border-radius:3px;background:#d9c39a}
.swatch-name{left:604px;top:358px;font-size:13px;color:var(--ink)}
.code{top:355px;height:25px;border:1px solid #c9c9c9;border-radius:4px;font-size:10px;display:flex;align-items:center;color:var(--text)}
.code span{padding:0 8px;height:100%;display:flex;align-items:center}
.code span+span{border-left:1px solid #c9c9c9}
.loc{top:642px;width:81px;height:35px;border:1px solid #c9c9c9;border-radius:4px;font-size:12px;display:flex;align-items:center;gap:8px;padding-left:12px;color:var(--text)}
.loc.sel{background:var(--green);border-color:var(--green);color:var(--white)}
.radio{width:13px;height:13px;border-radius:50%;border:1px solid #aaa}
.loc-img{left:884px;top:605px;width:119px;height:82px;border-radius:8px;background:linear-gradient(180deg,#ede1c2 0%,#c9ae78 70%,#8a5a44 100%)}
.qty{left:571px;top:770px;width:141px;height:40px;border:1px solid #c9c9c9;border-radius:5px;display:flex;align-items:center;justify-content:space-between;padding:0 9px;font-size:14px;font-weight:500;color:var(--ink)}
.price{left:803px;width:209px;height:35px;border-radius:18px;background:#eef3f1;display:flex;align-items:center;font-size:14px;color:var(--ink)}
.price .lab{flex:1;text-align:right;padding-right:10px;font-weight:500}
.price .val{width:85px;height:100%;background:var(--yellow);border-radius:0 18px 18px 0;font-weight:700;font-size:16px;display:flex;align-items:center;padding-left:11px}
.cta{top:858px;height:47px;border-radius:24px;font-size:17px;font-weight:600;text-align:center;line-height:47px}
.cta-cart{left:571px;width:216px;background:var(--yellow);color:var(--ink)}
.cta-quote{left:801px;width:217px;background:var(--green);color:var(--white)}

/* faq */
.faq{top:1640px;height:636px;background:var(--mint)}
.sec-title{width:1200px;text-align:center;font-size:38px;font-weight:800;color:var(--ink)}
.sec-rule{height:2px;background:var(--ink)}
.faq-list{left:159px;top:131px;width:884px;list-style:none}
.faq-list li{height:47.4px;border-bottom:1px solid var(--line);display:flex;align-items:center;justify-content:space-between;padding:0 12px 0 21px;font-size:17px;font-weight:500;color:var(--ink)}
.faq-list li:last-child{border-bottom:none}

/* reviews */
.reviews{top:2276px;height:468px}
.review{top:160px;width:284px;height:251px;border:1px solid #8fb8a9;border-radius:8px;padding:22px 18px 0 38px}
.quote{font-size:40px;font-weight:800;color:var(--green);line-height:30px;height:24px;margin-left:-20px}
.stars{display:flex;gap:2px;margin:4px 0 10px}
.review p{font-size:12px;font-weight:400;line-height:18px;color:var(--text)}
.review .name{position:absolute;left:38px;bottom:22px;font-size:12px;font-weight:700;color:var(--green);letter-spacing:.3px}
.arrow{top:263px}

/* delivery */
.delivery{top:2744px;height:149px;background:var(--green);text-align:center;color:var(--white);font-size:21px;line-height:34px;font-weight:500;padding-top:37px}
.delivery strong{color:var(--yellow);font-weight:800}

/* footer */
.footer{top:2893px;height:322px;background:var(--black);color:var(--white)}
.f-brand{left:150px;top:97px;font-size:25px;font-weight:700}
.f-col{top:46px}
.f-col h4{font-size:16px;font-weight:700;margin-bottom:9px}
.f-col a{display:block;font-size:12px;font-weight:400;color:#d8d8d8;text-decoration:none;line-height:22.5px}
.f-rule{left:150px;top:231px;width:900px;height:1px;background:#333}
.copy{top:270px;width:1200px;text-align:center;font-size:12px;color:#d8d8d8}
</style>
</head>
<body>

<header class="hero">
  <div class="abs brand">Custom Hat</div>
  <svg class="abs cart" width="28" height="26" viewBox="0 0 28 26" fill="none" stroke="#fff" stroke-width="1.8"><path d="M1 3h4l3 13h14l3-9H7"/><circle cx="10" cy="21" r="2"/><circle cx="20" cy="21" r="2"/></svg>
  <div class="abs cart-badge">0</div>
  <svg class="abs menu" width="22" height="18" viewBox="0 0 22 18" stroke="#fff" stroke-width="2"><path d="M0 2h22M0 9h22M0 16h22"/></svg>

  <h1 class="abs hero-title"><span class="accent">DESIGN</span><br>YOUR OWN<br>CAP</h1>
  <p class="abs hero-sub">Easily create and order custom caps<br>with your logo, colors, and style.</p>
  <div class="abs btn-hero">DESIGN YOUR CAP</div>

  <div class="abs tile t1" role="img" aria-label="Close-up of woven straw hat texture"></div>
  <div class="abs tile t2" role="img" aria-label="Woman in a straw hat sitting on a beach"></div>
  <div class="abs tile t3" role="img" aria-label="Person wearing a straw hat outdoors"></div>
  <div class="abs tile t4"></div>
  <div class="abs t4-img" role="img" aria-label="Straw lifeguard hat with colourful round patch, front and underside"></div>

  <span class="abs dot on" style="left:559px"></span>
  <span class="abs dot" style="left:581px"></span>
  <span class="abs dot" style="left:605px"></span>
  <span class="abs dot" style="left:629px"></span>
</header>

<section class="builder">
  <div class="abs card"></div>
  <div class="abs divider-v"></div>
  <h2 class="abs build-title">BUILD YOUR<br><span class="accent">PERFECT CAP</span></h2>
  <div class="abs build-rule"></div>
  <div class="abs hat-preview" role="img" aria-label="Preview of straw hat with yellow brim and round patch"></div>

  <div class="abs step-num" style="left:568px;top:95px">01</div>
  <div class="abs step-title" style="left:610px;top:99px">Choose Material</div>
  <div class="abs opt sel" style="left:568px;top:142px"><div class="opt-img" role="img" aria-label="Rush straw with mat sample" style="background:linear-gradient(135deg,#cdb98f,#9c8660)"></div></div>
  <div class="abs opt" style="left:683px;top:142px"><div class="opt-img" role="img" aria-label="Mat straw sample" style="background:linear-gradient(135deg,#a3a882,#6b7152)"></div></div>
  <div class="abs opt" style="left:798px;top:142px"><div class="opt-img" role="img" aria-label="Hollow straw sample" style="background:linear-gradient(135deg,#d6c697,#a8976a)"></div></div>
  <div class="abs opt" style="left:913px;top:142px"><div class="opt-img" role="img" aria-label="Rush straw sample" style="background:linear-gradient(135deg,#f4e7b2,#d6c07a)"></div></div>
  <svg class="abs check" style="left:657px;top:135px" viewBox="0 0 20 20"><circle cx="10" cy="10" r="10" fill="#5b9a85"/><path d="M5.5 10.5l3 3 6-6" stroke="#fff" stroke-width="2" fill="none"/></svg>
  <div class="abs opt-label" style="left:568px;top:226px">Rush Straw + mat</div>
  <div class="abs opt-label" style="left:683px;top:226px">Mat Straw</div>
  <div class="abs opt-label" style="left:798px;top:226px">Holow Straw</div>
  <div class="abs opt-label" style="left:913px;top:226px">Rush Straw</div>

  <div class="abs step-num" style="left:568px;top:275px">02</div>
  <div class="abs step-title" style="left:610px;top:279px">Choose Cap Color</div>
  <div class="abs slider"></div>
  <div class="abs knob"></div>
  <div class="abs swatch"></div>
  <div class="abs swatch-name">Sandle</div>
  <div class="abs code" style="left:701px"><span>Hex</span><span>#0062ff</span></div>
  <div class="abs code" style="left:798px"><span>RGB</span><span>0, 98, 25</span></div>
  <div class="abs code" style="left:902px"><span>CMYK</span><span>82, 65, 0, 0</span></div>

  <div class="abs step-num" style="left:568px;top:411px">03</div>
  <div class="abs step-title" style="left:608px;top:415px">Select Patch Shape</div>
  <div class="abs opt" style="left:568px;top:458px"><div class="opt-img" role="img" aria-label="Hat with round patch" style="background:linear-gradient(180deg,#f1e8d2,#d8c49a)"></div></div>
  <div class="abs opt" style="left:683px;top:458px"><div class="opt-img" role="img" aria-label="Hat with square patch" style="background:linear-gradient(180deg,#f3ebd6,#dccaa2)"></div></div>
  <div class="abs opt sel" style="left:798px;top:458px"><div class="opt-img" role="img" aria-label="Hat with rectangle patch" style="background:linear-gradient(180deg,#e6d2a6,#d9b84a)"></div></div>
  <div class="abs opt" style="left:913px;top:458px"><div class="opt-img" role="img" aria-label="Hat with custom patch" style="background:linear-gradient(180deg,#f2ead2,#cbb98a)"></div></div>
  <svg class="abs check" style="left:887px;top:451px" viewBox="0 0 20 20"><circle cx="10" cy="10" r="10" fill="#5b9a85"/><path d="M5.5 10.5l3 3 6-6" stroke="#fff" stroke-width="2" fill="none"/></svg>
  <div class="abs opt-label" style="left:568px;top:542px">Round</div>
  <div class="abs opt-label" style="left:683px;top:542px">Square</div>
  <div class="abs opt-label sel" style="left:798px;top:542px">Rectangle</div>
  <div class="abs opt-label" style="left:913px;top:542px">Custom</div>

  <div class="abs step-num" style="left:568px;top:592px">04</div>
  <div class="abs step-title" style="left:608px;top:596px">Select Patch Location</div>
  <div class="abs loc sel" style="left:571px"><svg width="16" height="16" viewBox="0 0 16 16"><circle cx="8" cy="8" r="8" fill="#fff"/><path d="M4.5 8.3l2.3 2.3 4.7-4.7" stroke="#5b9a85" stroke-width="1.8" fill="none"/></svg>Front</div>
  <div class="abs loc" style="left:672px"><span class="radio"></span>Side</div>
  <div class="abs loc" style="left:772px"><span class="radio"></span>Back</div>
  <div class="abs loc-img" role="img" aria-label="Straw hat showing front patch position"></div>

  <div class="abs step-num" style="left:568px;top:725px">05</div>
  <div class="abs step-title" style="left:608px;top:729px">Quantity</div>
  <div class="abs qty">
    <svg width="20" height="20" viewBox="0 0 20 20" fill="none" stroke="#333" stroke-width="1.3"><circle cx="10" cy="10" r="8.5"/><path d="M6 10h8"/></svg>
    25
    <svg width="20" height="20" viewBox="0 0 20 20" fill="none" stroke="#333" stroke-width="1.3"><circle cx="10" cy="10" r="8.5"/><path d="M6 10h8M10 6v8"/></svg>
  </div>
  <div class="abs price" style="top:733px"><span class="lab">Price per Unit:</span><span class="val">$10.00</span></div>
  <div class="abs price" style="top:782px"><span class="lab">Total 25 Unit:</span><span class="val">$250.00</span></div>

  <div class="abs cta cta-cart">Add to Cart</div>
  <div class="abs cta cta-quote">Request a Quote</div>
</section>

<section class="faq">
  <h2 class="abs sec-title" style="top:42px">FAQ</h2>
  <div class="abs sec-rule" style="left:561px;top:99px;width:79px"></div>
  <ul class="abs faq-list">
    <li>What types of materials can I choose for my custom cap?<svg width="20" height="20" viewBox="0 0 20 20" fill="none" stroke="#333" stroke-width="1.2"><circle cx="10" cy="10" r="8.5"/><path d="M6 10h8M10 6v8"/></svg></li>
    <li>Are palm leaf caps durable and comfortable?<svg width="20" height="20" viewBox="0 0 20 20" fill="none" stroke="#333" stroke-width="1.2"><circle cx="10" cy="10" r="8.5"/><path d="M6 10h8M10 6v8"/></svg></li>
    <li>Can I order just one custom cap?<svg width="20" height="20" viewBox="0 0 20 20" fill="none" stroke="#333" stroke-width="1.2"><circle cx="10" cy="10" r="8.5"/><path d="M6 10h8M10 6v8"/></svg></li>
    <li>Can I upload my own logo or design?<svg width="20" height="20" viewBox="0 0 20 20" fill="none" stroke="#333" stroke-width="1.2"><circle cx="10" cy="10" r="8.5"/><path d="M6 10h8M10 6v8"/></svg></li>
    <li>Where can I place the patch on the cap?<svg width="20" height="20" viewBox="0 0 20 20" fill="none" stroke="#333" stroke-width="1.2"><circle cx="10" cy="10" r="8.5"/><path d="M6 10h8M10 6v8"/></svg></li>
    <li>How long does it take to receive my custom caps?<svg width="20" height="20" viewBox="0 0 20 20" fill="none" stroke="#333" stroke-width="1.2"><circle cx="10" cy="10" r="8.5"/><path d="M6 10h8M10 6v8"/></svg></li>
    <li>Can I request a sample before placing a full order?<svg width="20" height="20" viewBox="0 0 20 20" fill="none" stroke="#333" stroke-width="1.2"><circle cx="10" cy="10" r="8.5"/><path d="M6 10h8M10 6v8"/></svg></li>
    <li>How is pricing calculated?<svg width="20" height="20" viewBox="0 0 20 20" fill="none" stroke="#333" stroke-width="1.2"><circle cx="10" cy="10" r="8.5"/><path d="M6 10h8M10 6v8"/></svg></li>
    <li>What if I need help designing my cap?<svg width="20" height="20" viewBox="0 0 20 20" fill="none" stroke="#333" stroke-width="1.2"><circle cx="10" cy="10" r="8.5"/><path d="M6 10h8M10 6v8"/></svg></li>
    <li>What’s your return or refund policy on custom caps?<svg width="20" height="20" viewBox="0 0 20 20" fill="none" stroke="#333" stroke-width="1.2"><circle cx="10" cy="10" r="8.5"/><path d="M6 10h8M10 6v8"/></svg></li>
  </ul>
</section>

<section class="reviews">
  <h2 class="abs sec-title" style="top:46px">REVIEWS</h2>
  <div class="abs sec-rule" style="left:560px;top:112px;width:80px"></div>

  <svg class="abs arrow" style="left:88px" width="32" height="32" viewBox="0 0 32 32" fill="none" stroke="#5b9a85" stroke-width="1.8"><circle cx="16" cy="16" r="14.5"/><path d="M22 16H10M15 11l-5 5 5 5"/></svg>
  <svg class="abs arrow" style="left:1077px" width="32" height="32" viewBox="0 0 32 32" fill="none" stroke="#5b9a85" stroke-width="1.8"><circle cx="16" cy="16" r="14.5"/><path d="M10 16h12M17 11l5 5-5 5"/></svg>

  <article class="abs review" style="left:150px">
    <div class="quote">“</div>
    <div class="stars"><svg width="80" height="14" viewBox="0 0 80 14" fill="#fcd535"><path id="st" d="M7 0l2 4.7 5 .4-3.8 3.3 1.2 5L7 10.8 2.6 13.4l1.2-5L0 5.1l5-.4z"/><use href="#st" x="16"/><use href="#st" x="32"/><use href="#st" x="48"/><use href="#st" x="64"/></svg></div>
    <p>We ordered 100 custom caps for our eco-retreat and went with the palm leaf material—absolutely stunning! The texture is unique, the patch placement was perfect, and our logo looked super clean. Great customer service too!</p>
    <div class="name">JORDAN REYES</div>
  </article>
  <article class="abs review" style="left:462px">
    <div class="quote">“</div>
    <div class="stars"><svg width="80" height="14" viewBox="0 0 80 14" fill="#fcd535"><use href="#st"/><use href="#st" x="16"/><use href="#st" x="32"/><use href="#st" x="48"/><use href="#st" x="64"/></svg></div>
    <p>The entire process was smooth. I customized our team caps with our brand color and a round patch on the front. They arrived faster than expected and looked even better in person. Highly recommend!</p>
    <div class="name">JORDAN REYES</div>
  </article>
  <article class="abs review" style="left:767px">
    <div class="quote">“</div>
    <div class="stars"><svg width="80" height="14" viewBox="0 0 80 14" fill="#fcd535"><use href="#st"/><use href="#st" x="16"/><use href="#st" x="32"/><use href="#st" x="48"/><use href="#st" x="64"/></svg></div>
    <p>I tried the raffia and palm leaf blend for a sustainable collection, and the craftsmanship really stood out. One cap had a small stitching issue, but they replaced it right away. Great experience overall!</p>
    <div class="name">JORDAN REYES</div>
  </article>
</section>

<section class="delivery">
  Custom caps delivered in <strong>10–21 business days,</strong> including production<br>and shipping—faster options and tracking available.
</section>

<footer class="footer">
  <div class="abs f-brand">Custom Hat</div>
  <nav class="abs f-col" style="left:362px"><h4>Shop</h4><a>Custom Caps</a><a>Eco-Friendly Materials</a><a>Patch Styles</a><a>Bulk Orders</a><a>Request a Quote</a></nav>
  <nav class="abs f-col" style="left:545px"><h4>Help</h4><a>FAQs</a><a>Sizing Guide</a><a>Design Assistance</a><a>Order Tracking</a><a>Contact Support</a></nav>
  <nav class="abs f-col" style="left:713px"><h4>Company</h4><a>About Us</a><a>Our Materials</a><a>Sustainability Commitment</a><a>Careers</a><a>Blog</a></nav>
  <nav class="abs f-col" style="left:918px"><h4>Legal</h4><a>Terms &amp; Conditions</a><a>Privacy Policy</a><a>Return &amp; Refund Policy</a><a>Shipping Policy</a></nav>
  <div class="abs f-rule"></div>
  <div class="abs copy">Copyright © 2025 All Rights Reserved</div>
</footer>

</body>
</html>
```